Logistics Website Design

See website https://tqfreightglobal.com for theme and color details. Need the site to be re-done and reflect some of the designs shown in this list here: https://pixelvane.com/tags/logistics-company-website

Target Market(s)

Logistics & Transportation

Industry/Entity Type

Logistics and Supply Chain

Coding

Number of Pages Required

5+ page

Requirements
Must have
• Colors must match theme of logo. Looking for a sleek, interactive design.

```html
<!DOCTYPE html>
<html lang="en">
<head>
<meta charset="utf-8">
<title>TQ Freight Global — Delivering Strength in Every Mile</title>
<link rel="stylesheet" href="https://fonts.googleapis.com/css2?family=PT+Sans:wght@400;700&display=swap">
<style>
:root{
  --bg:#0e0403;
  --bg-soft:#1a0b08;
  --orange:#e96c42;
  --orange-deep:#d85a30;
  --salmon:#c98a74;
  --ink:#1b0a06;
  --white:#ffffff;
  --line:#3a2520;
}
*{box-sizing:border-box;margin:0;padding:0}
html,body{width:1200px;height:4240px;overflow:hidden;background:var(--bg)}
body{position:relative;font-family:"PT Sans",sans-serif;color:var(--white)}
.abs{position:absolute}
.accent{color:var(--orange)}
.brand{display:flex;align-items:center;justify-content:center;flex-direction:column;gap:8px;background:#000;border-radius:4px}
.brand .dot{width:34px;height:34px;border-radius:50%;background:var(--orange)}
.brand .name{font-weight:700;font-size:15px;color:var(--orange);text-transform:uppercase;text-align:center;line-height:1.1}
.nav{display:flex;align-items:center;justify-content:space-around;background:var(--orange);border:2px solid #f3a283;border-radius:4px;transform:skewX(-8deg);padding:0 20px}
.nav a{transform:skewX(8deg);color:var(--ink);text-decoration:none;font-size:14px;font-weight:700;text-transform:uppercase}
.nav a.current{text-decoration:underline}
.btn{display:flex;align-items:center;justify-content:center;background:var(--orange);border:2px solid #f19a78;color:var(--ink);font-size:14px;font-weight:700;text-transform:uppercase;text-decoration:none}
.hero{left:0;top:137px;width:1200px;height:505px;background:linear-gradient(100deg,#3a2a22 0%,#5a4536 35%,#2f3f4c 65%,#1c2630 100%)}
.hero-band{left:0;top:636px;width:1200px;height:30px;background:var(--orange);clip-path:polygon(0 40%,100% 0,100% 30%,0 100%)}
.hero-title{left:113px;top:220px;width:520px;font-size:64px;line-height:68px;font-weight:700;text-transform:uppercase;letter-spacing:.5px}
.hero-sub{left:113px;top:444px;font-size:18px;font-weight:700}
.section-title{left:0;width:1200px;text-align:center;font-size:36px;font-weight:700;text-transform:uppercase}
.card{width:314px;height:446px;border-radius:18px;background:var(--salmon);color:var(--ink);text-align:center;padding:0 28px}
.card.active{background:var(--orange);border:2px solid #fff}
.card .icon{width:120px;height:88px;margin:38px auto 18px;background:var(--ink);border-radius:8px;opacity:.85}
.card h3{font-size:25px;line-height:30px;font-weight:400;text-transform:uppercase;margin-bottom:14px}
.card p{font-size:17px;line-height:30px}
.arrow{width:44px;height:44px;border:2px solid #fff;border-radius:50%}
.deco{background:linear-gradient(135deg,rgba(201,138,116,.25),rgba(201,138,116,0))}
.body-text{font-size:16px;line-height:30px;font-weight:700}
.story-photo{left:0;top:1786px;width:1200px;height:691px;background:linear-gradient(90deg,#2a1a12 0%,#3a3a3c 40%,#4c5560 75%,#2c3036 100%)}
.story-box{left:497px;top:1890px;width:663px;height:516px;background:rgba(18,8,6,.93);border-radius:16px;padding:48px 60px}
.story-box h2{font-size:36px;font-weight:700;text-transform:uppercase;margin-bottom:18px}
.story-box p{font-size:16px;line-height:32px;font-weight:700}
.cta-photo{left:601px;top:3313px;width:490px;height:384px;border:2px solid #fff;border-radius:16px;background:linear-gradient(135deg,#d9d6d2 0%,#8a8f98 55%,#31466a 100%)}
</style>
</head>
<body>

<header>
  <div class="abs brand" style="left:112px;top:8px;width:132px;height:117px"><span class="dot"></span><span class="name">TQ Freight<br>Global</span></div>
  <nav class="abs nav" style="left:368px;top:35px;width:723px;height:50px">
    <a class="current" href="#">Home</a><a href="#">Services</a><a href="#">Industries</a><a href="#">Request a Quote</a><a href="#">About Us</a><a href="#">Contact Us</a>
  </nav>
</header>

<section>
  <div class="abs hero" role="img" aria-label="Photo of a blue semi truck with a white trailer at a loading dock at dusk"></div>
  <div class="abs hero-band"></div>
  <h1 class="abs hero-title">Delivering<br><span class="accent">Strength</span> in<br>Every Mile</h1>
  <p class="abs hero-sub">Secure and reliable transportation for all your cargo needs.</p>
  <a class="abs btn" href="#" style="left:112px;top:502px;width:188px;height:43px">Request a Quote</a>
</section>

<section>
  <h2 class="abs section-title" style="top:732px">Our <span class="accent">Core</span> Services</h2>
  <div class="abs arrow" style="left:48px;top:1041px"><svg width="40" height="40" viewBox="0 0 40 40"><path d="M23 12l-8 8 8 8" fill="none" stroke="#fff" stroke-width="2"/></svg></div>
  <div class="abs arrow" style="left:1118px;top:1041px"><svg width="40" height="40" viewBox="0 0 40 40"><path d="M17 12l8 8-8 8" fill="none" stroke="#fff" stroke-width="2"/></svg></div>
  <article class="abs card active" style="left:113px;top:841px">
    <div class="icon" role="img" aria-label="Flatbed truck icon"></div>
    <h3>Flatbed<br>Transportation</h3>
    <p>From routine shipments to oversized and heavy-haul loads, we handle freight requiring proper securement, regulatory knowledge, and consistent on-time execution.</p>
  </article>
  <article class="abs card" style="left:444px;top:841px">
    <div class="icon" role="img" aria-label="Step deck truck icon"></div>
    <h3>Step Deck<br>Transportation</h3>
    <p>Our step deck trucking services support tall, heavy, and specialized freight that requires additional height clearance and flexible loading options.</p>
  </article>
  <article class="abs card" style="left:777px;top:841px">
    <div class="icon" role="img" aria-label="Dry van truck icon"></div>
    <h3>Dry Van<br>Transportation</h3>
    <p>From consumer goods to industrial materials, our dry van services provide the space, security, and consistency you need coast to coast.</p>
  </article>
</section>

<section>
  <div class="abs deco" style="left:0;top:1330px;width:230px;height:290px" role="img" aria-label="Decorative angled circuit lines"></div>
  <div class="abs deco" style="left:880px;top:1330px;width:320px;height:420px;transform:scaleX(-1) scaleY(-1)" role="img" aria-label="Decorative angled circuit lines"></div>
  <h2 class="abs section-title" style="top:1426px">Keeping Your <span class="accent">Supply Chain</span> Moving</h2>
  <p class="abs body-text" style="left:200px;top:1494px;width:800px;text-align:center">We deliver a comprehensive range of open-deck and specialized transportation services—including flatbed, step deck, heavy haul, and over-dimensional freight solutions. Backed by years of experience, a trusted nationwide carrier network, and a strong safety-first culture, we provide reliable, adaptable logistics support built around the unique requirements of every load.</p>
</section>

<section>
  <div class="abs" style="left:0;top:1774px;width:1200px;height:30px;background:var(--orange);clip-path:polygon(0 100%,100% 0,100% 60%,0 100%)"></div>
  <div class="abs story-photo" role="img" aria-label="Close-up photo of a truck's glowing headlight and wheels on wet pavement"></div>
  <div class="abs" style="left:0;top:2458px;width:1200px;height:30px;background:var(--orange);clip-path:polygon(0 0,100% 60%,100% 100%,0 60%)"></div>
  <div class="abs story-box">
    <h2>Our <span class="accent">Story</span></h2>
    <p>TQ Freight Global™ was born out of real-world experience in the fitness equipment industry. What started as a company shipping strength equipment, cardio machines, and training gear to gyms, schools, and commercial facilities quickly evolved into something bigger. As order volume grew and supply chains became more complex, the team developed deep expertise in coordinating freight, managing deliveries, and navigating the challenges of large-scale equipment transportation. That hands-on experience laid the foundation for what would eventually become a full-service logistics operation.</p>
    <a class="btn" href="#" style="width:186px;height:44px;margin-top:24px">Read More</a>
  </div>
</section>

<section>
  <div class="abs deco" style="left:0;top:2490px;width:140px;height:250px" role="img" aria-label="Decorative angled circuit lines"></div>
  <h2 class="abs section-title" style="top:2618px">Industries We <span class="accent">Power</span></h2>
  <div class="abs arrow" style="left:42px;top:2928px"><svg width="40" height="40" viewBox="0 0 40 40"><path d="M23 12l-8 8 8 8" fill="none" stroke="#fff" stroke-width="2"/></svg></div>
  <div class="abs arrow" style="left:1112px;top:2928px"><svg width="40" height="40" viewBox="0 0 40 40"><path d="M17 12l8 8-8 8" fill="none" stroke="#fff" stroke-width="2"/></svg></div>
  <article class="abs card active" style="left:113px;top:2727px;height:446px">
    <div class="icon" role="img" aria-label="Food and drink icon" style="width:80px;height:80px"></div>
    <h3>Food &amp; Beverage</h3>
    <p>TQ Freight Global provides reliable, compliant, and efficient trucking solutions for the food and beverage industry. We specialize in transporting national routes while maintaining strict quality and handling standards.</p>
  </article>
  <article class="abs card" style="left:444px;top:2727px;height:446px">
    <div class="icon" role="img" aria-label="Shopping cart with globe icon" style="width:80px;height:80px"></div>
    <h3>E-Commerce &amp;<br>Retail</h3>
    <p>Our E-Commerce &amp; Retail Trucking Services are designed to support the fast-paced logistics demands of modern online retailers, marketplaces, and brick-and-mortar brands.</p>
  </article>
  <article class="abs card" style="left:777px;top:2727px;height:446px">
    <div class="icon" role="img" aria-label="Shield with heartbeat icon" style="width:80px;height:80px"></div>
    <h3>Pharma &amp;<br>Healthcare</h3>
    <p>TQ Freight Global provides specialized transportation and supply chain solutions for pharmaceutical manufacturers, medical device companies, healthcare distributors, and reliability.</p>
  </article>
</section>

<section>
  <h2 class="abs" style="left:109px;top:3326px;font-size:36px;line-height:46px;font-weight:700;text-transform:uppercase">Let's Move Your <span class="accent">Business</span><br>Forward</h2>
  <p class="abs body-text" style="left:109px;top:3438px;width:460px;line-height:32px">Let's discuss your logistics needs and how we can help your business thriveWhat started as a company shipping strength equipment, cardio machines, and training gear to gyms, schools, and commercial facilities quickly evolved into something bigger.</p>
  <a class="abs btn" href="#" style="left:109px;top:3629px;width:187px;height:45px">Contact Us</a>
  <div class="abs cta-photo" role="img" aria-label="Photo of two dispatchers working at a computer with a map on screen"></div>
  <div class="abs deco" style="left:1030px;top:3700px;width:170px;height:110px;transform:scale(-1,-1)" role="img" aria-label="Decorative angled circuit lines"></div>
</section>

<footer>
  <div class="abs" style="left:0;top:3802px;width:1200px;height:1px;background:var(--line)"></div>
  <div class="abs brand" style="left:112px;top:3888px;width:186px;height:164px"><span class="dot" style="width:44px;height:44px"></span><span class="name" style="font-size:19px">TQ Freight<br>Global</span></div>
  <p class="abs body-text" style="left:364px;top:3888px;width:740px;font-size:16px;line-height:32px">TQ Freight Global™ was born out of real-world experience in the fitness equipment industry. What started as a company shipping strength equipment, cardio machines, and training gear to gyms, schools, and commercial facilities quickly evolved into something bigger.</p>
  <nav class="abs nav" style="left:368px;top:4011px;width:723px;height:50px">
    <a class="current" href="#">Home</a><a href="#">Services</a><a href="#">Industries</a><a href="#">Request a Quote</a><a href="#">About Us</a><a href="#">Contact Us</a>
  </nav>
  <div class="abs" style="left:0;top:4181px;width:1200px;height:1px;background:#5a4a46"></div>
  <p class="abs" style="left:0;top:4195px;width:1200px;text-align:center;font-size:16px;font-weight:700">© 2026. An independent agent of Halvern Ridge LLC.</p>
</footer>

</body>
</html>
```